Tallon Electrical Business Card

We need a business card design for our family-run electrical contracting business based in Western Australia called 'Tallon Electrical'. We provide electrical services including residential, commercial and industrial. We aim for individual business cards to be made for all of our employees. We already have a company logo, which we require to be featured on the design. We would like simple, sleek and vibrant designs, which incorporate our logo and represent our business. We do not want anything involving too many graphics/images. We like the colours red, black, white and all shades of grey. The final design should communicate professionalism and trustworthiness.
We require the following contact information:
Name- Grant Pellow
EC 5871
Mobile number- 0455 870 219
Fax number (including area code)- (08) 9560 2831
Email adress- name@tallonelectrical.com.au
Electrical
- ITC Handel Bold

```html
<!DOCTYPE html>
<html lang="en">
<head>
<meta charset="utf-8">
<title>Tallon Electrical Business Card</title>
<link href="https://fonts.googleapis.com/css2?family=Oswald:wght@500;600&family=Open+Sans:wght@400;600&display=swap" rel="stylesheet">
<style>
  :root {
    --red: #e3231b;
    --black: #111111;
    --white: #ffffff;
    --ink: #2a2a2a;
    --grey-bg: #d9d9d9;
  }
  * { margin: 0; padding: 0; box-sizing: border-box; }
  html, body { width: 1200px; height: 892px; overflow: hidden; }
  body {
    background: var(--grey-bg);
    position: relative;
    font-family: "Open Sans", sans-serif;
  }
  .card {
    position: absolute;
    width: 620px;
    height: 354px;
    overflow: hidden;
    box-shadow: 0 6px 18px rgba(0,0,0,0.18);
  }
  .card--front { left: 60px; top: 60px; background: var(--white); }
  .card--back { left: 520px; top: 478px; background: var(--black); }
  .card__shapes { position: absolute; inset: 0; width: 100%; height: 100%; }

  .brand {
    position: absolute;
    display: flex;
    align-items: center;
    gap: 12px;
  }
  .brand__mark { width: 30px; height: 30px; background: var(--red); }
  .brand__name {
    font-family: "Oswald", sans-serif;
    font-weight: 600;
    color: var(--ink);
    letter-spacing: 2px;
    text-transform: uppercase;
    white-space: nowrap;
  }
  .card--front .brand { left: 50%; top: 50%; transform: translate(-50%, -50%); }
  .card--front .brand__name { font-size: 34px; }
  .card--back .brand { right: 34px; top: 40px; gap: 9px; }
  .card--back .brand__mark { width: 22px; height: 22px; }
  .card--back .brand__name { font-size: 24px; }

  .person { position: absolute; left: 26px; top: 232px; }
  .person__name {
    font-family: "Oswald", sans-serif;
    font-weight: 500;
    font-size: 28px;
    color: var(--ink);
    letter-spacing: 0.5px;
    line-height: 1;
  }
  .person__role {
    font-family: "Oswald", sans-serif;
    font-weight: 500;
    font-size: 12px;
    letter-spacing: 2px;
    color: var(--ink);
    margin-top: 5px;
  }

  .contact {
    position: absolute;
    left: 300px;
    top: 160px;
    list-style: none;
    color: var(--white);
  }
  .contact__row { display: flex; align-items: center; gap: 12px; margin-bottom: 12px; }
  .contact__icon {
    width: 24px; height: 24px; border-radius: 50%;
    background: var(--white);
    display: flex; align-items: center; justify-content: center;
    flex-shrink: 0;
  }
  .contact__icon svg { width: 14px; height: 14px; }
  .contact__text { font-size: 11px; line-height: 1.35; }
</style>
</head>
<body>

<section class="card card--front" aria-label="Business card front">
  <div class="brand">
    <span class="brand__mark"></span>
    <span class="brand__name">Tallon Electrical</span>
  </div>
</section>

<section class="card card--back" aria-label="Business card back">
  <svg class="card__shapes" viewBox="0 0 620 354" preserveAspectRatio="none" aria-hidden="true">
    <polygon points="150,150 620,92 620,300 400,354 250,354" fill="var(--red)"/>
    <polygon points="320,0 620,0 620,104 196,156" fill="var(--white)"/>
    <polyline points="190,162 620,110" stroke="var(--red)" stroke-width="4" fill="none"/>
    <polygon points="0,100 262,236 0,354" fill="var(--white)" stroke="var(--red)" stroke-width="4"/>
    <polygon points="420,354 620,304 620,354" fill="var(--black)"/>
  </svg>

  <div class="brand">
    <span class="brand__mark"></span>
    <span class="brand__name">Tallon Electrical</span>
  </div>

  <div class="person">
    <p class="person__name">GRANT PELLOW</p>
    <p class="person__role">GENERAL MANAGER</p>
  </div>

  <ul class="contact">
    <li class="contact__row">
      <span class="contact__icon">
        <svg viewBox="0 0 16 16"><path d="M8 2 L15 8 H13 V14 H9.5 V10 H6.5 V14 H3 V8 H1 Z" fill="var(--red)"/></svg>
      </span>
      <span class="contact__text">12 Kestrel Road,<br>Malaga WA 6090</span>
    </li>
    <li class="contact__row">
      <span class="contact__icon">
        <svg viewBox="0 0 16 16"><path d="M4 1h8v14H4z" fill="var(--red)"/><rect x="5.5" y="3" width="5" height="8" fill="var(--white)"/></svg>
      </span>
      <span class="contact__text">0455 870 219<br>(08) 9560 2831</span>
    </li>
    <li class="contact__row">
      <span class="contact__icon">
        <svg viewBox="0 0 16 16"><circle cx="8" cy="8" r="6.5" fill="none" stroke="var(--red)" stroke-width="1.5"/><ellipse cx="8" cy="8" rx="2.8" ry="6.5" fill="none" stroke="var(--red)" stroke-width="1.2"/><line x1="1.5" y1="8" x2="14.5" y2="8" stroke="var(--red)" stroke-width="1.2"/></svg>
      </span>
      <span class="contact__text">name@tallonelectrical.com.au<br>www.tallonelectrical.com.au</span>
    </li>
  </ul>
</section>

</body>
</html>
```